Label Design for Saffron Company

We need a label design that is unique for our container. The item inside the container is Saffron, and it is 5g in weigh. We need on the label our logo, the weight and quality. Here is the exactly what we want. We want the background to be black for the label and the design to present royalty, and premium quality.

Premium Quality
Grade A+ Premium Saffron
100% Natural and Pure
www.VelmoraSpice.com

Target Market(s)

Everyone

Requirements
Must have
• Black background, golden border design. Unique design, that show premium and royalty.
Nice to have
• The logo is attached with transparent background so you can show exactly how things look like.
Should not have
• different colors that are not part of the logo.

```html
<!DOCTYPE html>
<html lang="en">
<head>
<meta charset="utf-8">
<title>Velmora Spice – Saffron Lid Label</title>
<link rel="stylesheet" href="https://fonts.googleapis.com/css2?family=Marcellus&family=Archivo:wght@900&family=Tinos&display=swap">
<style>
  :root {
    --page-bg: #ffffff;
    --label-black: #0c0c0c;
    --damask-tone: #1d1d1d;
    --gold-light: #f3e3a6;
    --gold-mid: #c9a95b;
    --gold-deep: #8a6a2c;
    --ink-white: #f4f4f2;
    --ink-dark: #1a1a1a;
  }
  html, body {
    margin: 0;
    padding: 0;
    width: 720px;
    height: 1200px;
    overflow: hidden;
    background: var(--page-bg);
  }
  .label-canvas {
    display: block;
    width: 720px;
    height: 1200px;
  }
  .brand-name {
    font-family: "Marcellus", serif;
    fill: var(--ink-white);
    text-anchor: middle;
    letter-spacing: 6px;
  }
  .brand-name--top { font-size: 36px; }
  .brand-name--main { font-size: 48px; letter-spacing: 4px; }
  .quality-title {
    font-family: "Marcellus", serif;
    fill: var(--gold-mid);
    font-size: 64px;
    text-anchor: middle;
  }
  .grade-line {
    font-family: "Marcellus", serif;
    fill: var(--ink-white);
    font-size: 35px;
    text-anchor: middle;
  }
  .purity-figure {
    font-family: "Archivo", sans-serif;
    font-weight: 900;
    fill: var(--ink-dark);
    font-size: 112px;
  }
  .purity-words {
    font-family: "Marcellus", serif;
    fill: var(--ink-dark);
    font-size: 52px;
  }
  .web-address {
    font-family: "Tinos", serif;
    fill: var(--ink-white);
    font-size: 23px;
    text-anchor: middle;
  }
  .net-weight {
    font-family: "Tinos", serif;
    fill: var(--gold-mid);
    font-size: 28px;
    text-anchor: middle;
  }
</style>
</head>
<body>
<svg class="label-canvas" viewBox="0 0 720 1200" xmlns="http://www.w3.org/2000/svg">
  <defs>
    <linearGradient id="gold-rim" x1="0" y1="0" x2="1" y2="1">
      <stop offset="0" stop-color="var(--gold-light)"/>
      <stop offset="0.45" stop-color="var(--gold-mid)"/>
      <stop offset="0.75" stop-color="var(--gold-deep)"/>
      <stop offset="1" stop-color="var(--gold-light)"/>
    </linearGradient>
    <linearGradient id="gold-band" x1="0" y1="0" x2="1" y2="0">
      <stop offset="0" stop-color="var(--gold-deep)"/>
      <stop offset="0.2" stop-color="var(--gold-mid)"/>
      <stop offset="0.55" stop-color="var(--gold-light)"/>
      <stop offset="0.8" stop-color="var(--gold-mid)"/>
      <stop offset="1" stop-color="var(--gold-deep)"/>
    </linearGradient>
    <radialGradient id="damask-field" cx="0.5" cy="0.4" r="0.6">
      <stop offset="0" stop-color="var(--damask-tone)"/>
      <stop offset="1" stop-color="var(--label-black)"/>
    </radialGradient>
    <clipPath id="label-face">
      <circle cx="360" cy="600" r="318"/>
    </clipPath>
  </defs>

  <!-- label rim and face -->
  <circle class="label-rim" cx="360" cy="600" r="332" fill="url(#gold-rim)"/>
  <circle class="label-face" cx="360" cy="600" r="318" fill="var(--label-black)"/>
  <circle class="damask-background" cx="360" cy="600" r="318" fill="url(#damask-field)"
          role="img" aria-label="Dark grey damask pattern across the black label face"/>

  <!-- dotted gold ring -->
  <path class="dot-ring" d="M 82 690 A 292 292 0 1 1 638 690"
        fill="none" stroke="var(--gold-mid)" stroke-width="10"
        stroke-linecap="round" stroke-dasharray="0 21"/>

  <!-- brand mark placeholder and name -->
  <rect class="brand-square" x="313" y="334" width="94" height="94" rx="12"
        fill="none" stroke="var(--gold-mid)" stroke-width="2"/>
  <text class="brand-name brand-name--top" x="360" y="480">VELMORA</text>
  <text class="brand-name brand-name--main" x="360" y="532">SPICE</text>

  <line class="divider" x1="92" y1="554" x2="628" y2="554" stroke="var(--gold-mid)" stroke-width="1.5"/>

  <!-- quality statements -->
  <text class="quality-title" x="360" y="623" textLength="512" lengthAdjust="spacingAndGlyphs">Premium Quality</text>
  <text class="grade-line" x="360" y="669" textLength="480" lengthAdjust="spacingAndGlyphs">Grade A+  Premium Saffron</text>

  <!-- purity band -->
  <g clip-path="url(#label-face)">
    <rect class="purity-band" x="20" y="692" width="680" height="114" fill="url(#gold-band)"/>
  </g>
  <text class="purity-figure" x="134" y="793" textLength="222" lengthAdjust="spacingAndGlyphs">100%</text>
  <text class="purity-words" x="372" y="743" textLength="176" lengthAdjust="spacingAndGlyphs">Natural</text>
  <text class="purity-words" x="372" y="795" textLength="214" lengthAdjust="spacingAndGlyphs">and Pure</text>

  <!-- footer -->
  <text class="web-address" x="360" y="846" textLength="258" lengthAdjust="spacingAndGlyphs">www.VelmoraSpice.com</text>
  <text class="net-weight" x="360" y="880">5 gram</text>
</svg>
</body>
</html>
```